Bright Harbor Goods - Product Page

Looking for a design for our product pages to showcase all of the following information in an aesthetically pleasing way. <br/><br/>• Product price per piece & price breaks<br/>• Set up cost <br/>• Additional color cost<br/>• Imprint side <br/>• Product Dimensions<br/><br/>Attached are photos showing ideas we have come up with to display the information. <br/><br/>The link below shows how our product pages is currently laid out. <br/><br/>Link to webpage: https://www.brightharborgoods-example.com/non-woven-reusable-promo-totes.html<br/>

Number of Pages Required

1 page

Colors
33b8a4
33a6d7
3277b5
fece3e
f9a040
a3cd3a

Requirements
Must have
• • Product price per piece & price breaks
• • Set up cost
• • Additional color cost
• • Imprint side
• • Product Dimensions

```html
<!DOCTYPE html>
<html lang="en">
<head>
<meta charset="utf-8">
<title>Bright Harbor Goods – Non-Woven Reusable Promo Totes</title>
<link href="https://fonts.googleapis.com/css2?family=Poppins:wght@400;500;600;700&display=swap" rel="stylesheet">
<style>
:root{
  --navy:#0b4a74;
  --green:#6bb33f;
  --leaf:#a3cd3a;
  --sky:#33a6d7;
  --teal:#33b8a4;
  --yellow:#fece3e;
  --orange:#f9a040;
  --red:#e8341c;
  --star:#f00;
  --grey:#7a7a7a;
  --line:#d8d8d8;
  --ink:#222;
  --pale:#f4f4f4;
}
*{box-sizing:border-box;margin:0;padding:0}
html,body{width:1200px;height:2860px;overflow:hidden}
body{font-family:'Poppins',sans-serif;color:var(--ink);background:#fff;position:relative}
.abs{position:absolute}
a{color:inherit;text-decoration:none}

.topbar{left:0;top:0;width:1200px;height:51px;background:var(--navy);color:#fff;font-size:15px;font-weight:500}
.topbar .welcome{position:absolute;left:111px;top:14px}
.topbar .social{position:absolute;right:111px;top:18px;display:flex;gap:14px}
.dot{width:14px;height:14px;border-radius:50%;background:#fff;display:block}

.header{left:0;top:51px;width:1200px;height:118px;background:var(--pale)}
.brand{position:absolute;left:111px;top:32px;font-size:30px;font-weight:700;color:var(--green);line-height:1}
.brand small{display:block;font-size:20px;color:var(--orange);text-align:right;margin-top:2px}
.rush{position:absolute;left:378px;top:20px;width:80px;height:80px;border-radius:50%;background:var(--red);color:#fff;text-align:center;font-weight:700;font-size:15px;line-height:16px;padding-top:18px;box-shadow:0 0 0 4px #f7b7ad}
.rush span{display:block;font-size:9px;font-weight:500}
.call{position:absolute;left:490px;top:33px;color:var(--green);font-weight:600;font-size:16px}
.call b{display:block;color:var(--orange);font-size:21px;font-weight:700;margin-top:2px}
.cart{position:absolute;left:695px;top:28px;display:flex;align-items:center;gap:4px}
.cart em{font-style:normal;background:var(--green);color:#fff;font-size:11px;padding:0 6px;border-radius:3px}
.search{position:absolute;left:752px;top:24px;width:336px;height:32px;background:#fff;border:1px solid var(--line);font-size:11px;color:#888;padding:8px 10px}
.search svg{position:absolute;right:6px;top:6px}
.links{position:absolute;right:111px;top:75px;display:flex;gap:28px;font-size:16px;font-weight:500}

.nav{left:0;top:169px;width:1200px;height:62px;background:var(--green);color:#fff;font-weight:600;font-size:16.5px;display:flex;justify-content:space-between;padding:20px 111px 0}

.photo{left:111px;top:303px;width:423px;height:430px;border:1px solid #999;background:linear-gradient(120deg,#fff 20%,#e53935 21%,#e53935 45%,#d9c79e 46%,#cdb98c 75%,#fff 76%)}
.thumbs{left:111px;top:766px;width:423px;display:grid;grid-template-columns:repeat(5,77px);gap:19px 9.5px}
.thumb{height:67px;border:1px solid #888;background:#fff;position:relative}
.thumb i{position:absolute;left:25px;top:18px;width:27px;height:38px;border-radius:2px;background:var(--c)}

.info{left:566px;top:300px;width:521px}
.sku{font-size:18px;color:var(--navy);font-weight:500}
.title{font-size:29px;color:var(--green);font-weight:600;margin-top:6px}
.spec{font-size:16px;margin-top:10px;display:flex;align-items:center;gap:8px}
.stars{color:var(--star);letter-spacing:1px}
.revline{font-size:16px;margin-top:4px}
.revline span{color:var(--orange);font-weight:600}

.price{width:521px;border:1px solid var(--navy);margin-top:0}
.price h3{background:var(--navy);color:#fff;font-weight:600;font-size:16px;text-align:center;height:46px;line-height:46px}
.price table{width:100%;border-collapse:collapse;font-size:14px}
.price td{border:1px solid var(--line);text-align:center;height:42px}
.price1{top:460px;left:566px;position:absolute}
.price2{top:606px;left:566px;position:absolute}

.prod{position:absolute;top:751px;width:257px;height:279px;border:1px solid #888}
.prod.instock{left:566px}.prod.overseas{left:832px}
.prod header{height:68px;color:#fff;text-align:center;font-weight:600;font-size:18px;padding-top:10px}
.prod header small{display:block;font-size:11.5px;font-weight:400;font-style:italic;margin-top:2px}
.instock header{background:var(--sky)}.overseas header{background:var(--teal)}
.prod .incl{background:var(--yellow);height:42px;line-height:42px;text-align:center;font-weight:600;font-size:15px;color:var(--navy)}
.prod dl{font-size:14px;padding:0 4px 0 13px}
.prod dl div{display:flex;justify-content:space-between;height:41px;align-items:center;border-bottom:1px solid var(--line)}
.prod dl div:last-child{border:0}
.prod dd{color:#444}

.btns{position:absolute;top:1061px;left:568px;display:flex;gap:12px}
.btn{width:165px;height:58px;line-height:58px;text-align:center;color:#fff;font-weight:600;font-size:17px;border-radius:2px}
.btn.quote{background:var(--green)}.btn.buy{background:var(--yellow)}.btn.sample{background:var(--navy)}

.reviews{left:565px;top:1180px;width:522px}
.reviews h2{font-size:28px;color:var(--green);font-weight:600}
.review{border-bottom:1px solid var(--line);padding:18px 0 22px}
.review h4{color:var(--navy);font-size:17px;font-weight:600}
.review .stars{font-size:24px;margin:2px 0 6px;letter-spacing:3px}
.review p{font-size:16px;color:#333}
.seeall{display:inline-block;margin-top:18px;font-size:16px;border-bottom:1px solid #333;color:#333}

.acc{left:568px;width:519px;height:58px;color:#fff;font-size:21px;font-weight:600;padding:14px 15px;display:flex;justify-content:space-between;background:var(--grey);box-shadow:0 2px 3px rgba(0,0,0,.2)}
.acc.open{background:var(--green)}

.band{left:0;top:1895px;width:1200px;height:525px;background:var(--pale)}
.rec-title{left:0;top:1955px;width:1200px;text-align:center;font-size:36px;font-weight:600;color:var(--green)}
.card{top:2064px;width:269px;height:282px;background:#fff;border:1px solid #888;text-align:center;font-size:16px;color:#333;line-height:24px}
.card .pic{width:130px;height:120px;margin:18px auto 28px;border-radius:4px}
.card .stars{font-size:20px}
.arrow{top:2195px}

.footer{left:0;top:2420px;width:1200px;height:380px;background:linear-gradient(135deg,#0d3d63,#1b4f78 55%,#123f66);color:#fff}
.footer .fbrand{position:absolute;left:12px;top:65px;font-size:32px;font-weight:700;line-height:1}
.footer .fbrand small{display:block;font-size:22px;text-align:right;margin-top:2px}
.footer .about{position:absolute;left:12px;top:150px;width:280px;font-size:13.5px;line-height:19px}
.footer .fsoc{position:absolute;left:12px;top:272px;display:flex;gap:12px}
.footer .fsoc .dot{width:11px;height:11px}
.fcol{position:absolute;top:68px}
.fcol h5{font-size:18px;font-weight:600;margin-bottom:18px}
.fcol ul{list-style:none;font-size:13px;line-height:27px;padding-left:8px}
.fcol p{font-size:13px;line-height:18px;margin-bottom:36px}
.bottombar{left:0;top:2800px;width:1200px;height:60px;background:var(--navy);color:#fff;font-size:13px;text-align:center;line-height:60px}
.chat{left:1026px;top:2790px;width:174px;height:70px;display:flex;align-items:center}
.chat .avatar{width:66px;height:66px;border-radius:50%;background:#c9d9e8;border:3px solid #fff;position:relative;z-index:1}
.chat .label{margin-left:-14px;background:var(--leaf);color:#fff;font-size:12.5px;font-weight:600;line-height:15px;padding:10px 8px 10px 24px;border-radius:0 0 0 30px;height:56px;text-align:center}
</style>
</head>
<body>

<div class="abs topbar">
  <span class="welcome">Welcome To Bright Harbor Goods!</span>
  <div class="social"><i class="dot"></i><i class="dot"></i><i class="dot"></i><i class="dot"></i><i class="dot"></i><i class="dot"></i></div>
</div>

<div class="abs header">
  <div class="brand">Bright Harbor<small>Goods</small></div>
  <div class="rush">FREE<br>RUSH<span>Click Here</span></div>
  <div class="call">Call Us Toll Free:<b>1-800-555-0142</b></div>
  <div class="cart">
    <svg width="17" height="14" viewBox="0 0 17 14"><path d="M0 1h3l2 8h9l2-6H4" fill="none" stroke="#222" stroke-width="2"/><circle cx="6" cy="12" r="1.5"/><circle cx="13" cy="12" r="1.5"/></svg>
    <em>0</em>
  </div>
  <div class="search">SEARCH ENTIRE STORE HERE...
    <svg width="18" height="18" viewBox="0 0 18 18"><circle cx="7" cy="7" r="5" fill="none" stroke="#6bb33f" stroke-width="2.5"/><path d="M11 11l5 5" stroke="#6bb33f" stroke-width="3"/></svg>
  </div>
  <nav class="links"><a>Home</a><a>About Us</a><a>Contact Us</a><a>Blog</a></nav>
</div>

<nav class="abs nav"><a>REUSABLE BAGS</a><a>SEED PAPER</a><a>REUSABLE BOTTLES</a><a>LANYARDS</a><a>ECO PROMO ITEMS</a></nav>

<div class="abs photo" role="img" aria-label="Photo of a red and a tan non-woven promo tote bag with printed logos"></div>

<div class="abs thumbs">
  <div class="thumb"><i style="--c:#222"></i></div>
  <div class="thumb"><i style="--c:#1d5a3a"></i></div>
  <div class="thumb"><i style="--c:#1f9a6a"></i></div>
  <div class="thumb"><i style="--c:#78cc52"></i></div>
  <div class="thumb"><i style="--c:#1b8cd0"></i></div>
  <div class="thumb"><i style="--c:#1f2f8a"></i></div>
  <div class="thumb"><i style="--c:#e53935"></i></div>
  <div class="thumb"><i style="--c:#2b2fa0"></i></div>
  <div class="thumb"><i style="--c:#c7b38c"></i></div>
  <div class="thumb"><i style="--c:#1cc2c9"></i></div>
  <div class="thumb"><i style="--c:#f3d34a"></i></div>
  <div class="thumb"><i style="--c:#5a34b0"></i></div>
</div>

<div class="abs info">
  <div class="sku">SKU: PP2</div>
  <h1 class="title">Non-Woven Reusable Promo Totes</h1>
  <div class="spec">Size:&nbsp; 13" W x 14" H x 7" D | &nbsp;Thickness: 100 GSM <span class="stars">★★★★★</span></div>
  <div class="revline"><span>38 Review(s)</span> &nbsp;| &nbsp;Add Review</div>
</div>

<div class="price price1">
  <h3>In-Stock</h3>
  <table>
    <tr><td>Qty</td><td>1</td><td>100+</td><td>250+</td><td>500+</td><td>1,000+</td><td>2,500+</td><td>5,000+</td></tr>
    <tr><td>Price</td><td>$0.69</td><td>$1.46</td><td>$0.69</td><td>$1.46</td><td>$0.69</td><td>$1.46</td><td>$0.69</td></tr>
  </table>
</div>
<div class="price price2">
  <h3>Overseas</h3>
  <table>
    <tr><td>Qty</td><td>1</td><td>100+</td><td>250+</td><td>500+</td><td>1,000+</td><td>2,500+</td><td>5,000+</td></tr>
    <tr><td>Price</td><td>$0.69</td><td>$1.46</td><td>$0.69</td><td>$1.46</td><td>$0.69</td><td>$1.46</td><td>$0.69</td></tr>
  </table>
</div>

<section class="prod instock">
  <header>In Stock Production<small>Orders of 100 pcs or more</small></header>
  <div class="incl">Includes 1 imprint color</div>
  <dl>
    <div><dt>Imprint Size:</dt><dd>8" W x 8" H</dd></div>
    <div><dt>Additional Colors:</dt><dd>$0.45 each</dd></div>
    <div><dt>Full Color Imprint</dt><dd>$1.00 each</dd></div>
    <div><dt>Set Up Fee:</dt><dd>$45 per color</dd></div>
  </dl>
</section>
<section class="prod overseas">
  <header>Overseas Production<small>Orders of 100 pcs or more</small></header>
  <div class="incl">Free 1color 2 Location Imprint</div>
  <dl>
    <div><dt>Imprint Size:</dt><dd>8" W x 8" H</dd></div>
    <div><dt>Additional Colors:</dt><dd>$0.45 each</dd></div>
    <div><dt>Full Color Imprint</dt><dd>$1.00 each</dd></div>
    <div><dt>Set Up Fee:</dt><dd>$45 per color</dd></div>
  </dl>
</section>

<div class="btns">
  <a class="btn quote">Request A Quote</a>
  <a class="btn buy">Buy Now</a>
  <a class="btn sample">Order Free Sample</a>
</div>

<section class="abs reviews">
  <h2>Customer Reviews (38)</h2>
  <article class="review"><h4>Review by Dana R</h4><div class="stars">★★★★★</div><p>Really thrilled with the bags!&nbsp; The printed was exceptional.</p></article>
  <article class="review"><h4>Review by Dana R</h4><div class="stars">★★★★★</div><p>Really thrilled with the bags!&nbsp; The printed was exceptional.</p></article>
  <a class="seeall">See all 38 customer reviews</a>
</section>

<div class="abs acc open" style="top:1546px">Product Detail<span>+</span></div>
<div class="abs acc" style="top:1615px">Reviews<span>+</span></div>
<div class="abs acc" style="top:1684px">Additional Info<span>+</span></div>
<div class="abs acc" style="top:1753px">Shipping Estimator<span>+</span></div>

<div class="abs band"></div>
<h2 class="abs rec-title">Recommended Products</h2>

<svg class="abs arrow" style="left:60px" width="28" height="50" viewBox="0 0 28 50"><path d="M25 3L4 25l21 22" fill="none" stroke="#333" stroke-width="3"/></svg>
<svg class="abs arrow" style="left:1120px" width="28" height="50" viewBox="0 0 28 50"><path d="M3 3l21 22L3 47" fill="none" stroke="#333" stroke-width="3"/></svg>

<div class="abs card" style="left:149px">
  <div class="pic" role="img" aria-label="Green and red promo tote bags" style="background:linear-gradient(90deg,#2fc24a 50%,#e53935 50%)"></div>
  Size :&nbsp; 16" W x 12" H x 6" D<br>As Low As: $0.54<br>SKU: pp9<br><span class="stars">★★★★★</span>
</div>
<div class="abs card" style="left:466px">
  <div class="pic" role="img" aria-label="Purple and tan promo tote bags" style="background:linear-gradient(90deg,#6a4fb0 50%,#e9d7b2 50%)"></div>
  Size :&nbsp; 16" W x 12" H x 6" D<br>As Low As: $0.54<br>SKU: pp9<br><span class="stars">★★★★★</span>
</div>
<div class="abs card" style="left:782px">
  <div class="pic" role="img" aria-label="Blue and red promo tote bags" style="background:linear-gradient(90deg,#1b78c8 50%,#e53935 50%)"></div>
  Size :&nbsp; 16" W x 12" H x 6" D<br>As Low As: $0.54<br>SKU: pp9<br><span class="stars">★★★★★</span>
</div>

<footer class="abs footer">
  <div class="fbrand">Bright Harbor<small>Goods</small></div>
  <p class="about">Bright Harbor Goods is an eco-friendly company that specializes in manufacturing custom bags. BHG was founded in 2009 and has strived to make the world a better place ever since.</p>
  <div class="fsoc"><i class="dot"></i><i class="dot"></i><i class="dot"></i><i class="dot"></i><i class="dot"></i></div>
  <div class="fcol" style="left:313px"><h5>USEFUL LINKS</h5>
    <ul><li>Customer Service</li><li>Our Story</li><li>Site Map</li><li>FTC Disclosure</li><li>Privacy Policy</li><li>Contact Us</li><li>Art &amp; Imprint Policy</li><li>Free Rush</li></ul></div>
  <div class="fcol" style="left:614px"><h5>WHY BUY FROM US</h5>
    <ul><li>Reusable Bag Stats</li><li>Best Price Guarantee</li><li>Return &amp; Refund Policy</li><li>Shipping Policy</li><li>In-Stock &amp; Custom Production</li><li>Frequently Asked Questions</li></ul></div>
  <div class="fcol" style="left:915px"><h5>ADDRESS</h5>
    <p>450 Harbor Way, Suite 8<br>Port Ellis, FL 33000</p>
    <p>Phone: 1-800-555-0142</p>
    <p>Email: hello@brightharborgoods-example.com</p></div>
</footer>
<div class="abs bottombar">© 2020 BrightHarborGoods-example.com</div>

<div class="abs chat">
  <div class="avatar" role="img" aria-label="Support agent portrait"></div>
  <div class="label">LEAVE<br>A MESSAGE</div>
</div>

</body>
</html>
```